Business Card - Tidal Lanes

Need Business Card design for company named Tidal Lanes. Software development focused mainly on Brindle Orvix & Zelt Apps. I've attached our logo with both a black and white background. Please add trademark symbol to logo when using.

```html
<!DOCTYPE html>
<html lang="en">
<head>
<meta charset="utf-8">
<title>Tidal Lanes – Business Card</title>
<link href="https://fonts.googleapis.com/css2?family=Open+Sans:wght@400;600;700&display=swap" rel="stylesheet">
<style>
  :root {
    --page-bg: #e4e4ea;
    --card-black: #050505;
    --brand-red: #d81c16;
    --brand-yellow: #f6b800;
    --brand-orange: #f7912e;
    --back-orange: #fb9a35;
    --back-glow: #fbc10f;
    --text-white: #ffffff;
    --divider: #6a6a6a;
  }
  * { margin: 0; padding: 0; box-sizing: border-box; }
  html, body { width: 1200px; height: 987px; overflow: hidden; }
  body {
    background: var(--page-bg);
    font-family: "Open Sans", Arial, sans-serif;
    display: flex;
    flex-direction: column;
    align-items: center;
    justify-content: center;
    gap: 27px;
  }
  .card {
    position: relative;
    width: 788px;
    height: 450px;
    border-radius: 28px;
    overflow: hidden;
  }

  /* Front */
  .card-front { background: var(--card-black); color: var(--text-white); }
  .front-swoosh { position: absolute; inset: 0; }
  .brand-block {
    position: absolute;
    left: 150px;
    top: 150px;
    display: flex;
    align-items: center;
    gap: 14px;
  }
  .brand-dot {
    width: 22px; height: 22px; border-radius: 50%;
    background: var(--brand-orange);
  }
  .brand-name {
    font-weight: 700;
    font-size: 46px;
    letter-spacing: -1px;
    color: var(--text-white);
  }
  .brand-name sup { font-size: 14px; font-weight: 700; vertical-align: super; }
  .holder {
    position: absolute;
    left: 58px;
    top: 328px;
    line-height: 1.15;
  }
  .holder-name { font-weight: 700; font-size: 24px; }
  .holder-title { font-weight: 400; font-size: 20px; padding-left: 8px; }
  .divider {
    position: absolute;
    left: 440px; top: 100px;
    width: 2px; height: 150px;
    background: var(--divider);
  }
  .contact {
    position: absolute;
    left: 478px;
    top: 112px;
    list-style: none;
    font-size: 24px;
    line-height: 1.45;
  }
  .contact li { display: flex; align-items: center; gap: 12px; }
  .contact svg { width: 20px; height: 22px; flex: none; }
  .address { padding-left: 0; margin-top: 6px; }

  /* Back */
  .card-back {
    background: radial-gradient(circle at 42% 45%, var(--back-glow) 0%, var(--back-orange) 65%);
    color: var(--text-white);
    display: flex;
    flex-direction: column;
    align-items: center;
    justify-content: center;
    gap: 30px;
  }
  .back-brand { display: flex; align-items: center; gap: 18px; }
  .back-brand .brand-dot { width: 30px; height: 30px; background: var(--text-white); }
  .back-brand .brand-name { font-size: 64px; }
  .website { font-size: 26px; letter-spacing: 2px; }
</style>
</head>
<body>

  <section class="card card-front" aria-label="Business card front">
    <svg class="front-swoosh" viewBox="0 0 788 450" preserveAspectRatio="none" aria-hidden="true">
      <path d="M0 255 C160 270 260 330 330 400 C370 440 420 450 460 450 L0 450 Z" fill="var(--brand-red)"/>
      <path d="M0 238 C170 250 280 320 340 385 C390 435 520 430 788 395 L788 403 C540 440 390 450 330 400 C260 330 160 270 0 255 Z" fill="var(--brand-yellow)"/>
      <path d="M420 450 C560 440 680 420 788 405 L788 450 Z" fill="var(--brand-orange)"/>
      <path d="M430 450 C560 442 680 428 788 415 L788 450 Z" fill="var(--brand-red)"/>
    </svg>

    <div class="brand-block">
      <span class="brand-dot"></span>
      <span class="brand-name">Tidal Lanes<sup>™</sup></span>
    </div>

    <div class="holder">
      <div class="holder-name">Your Name</div>
      <div class="holder-title">Title</div>
    </div>

    <div class="divider"></div>

    <ul class="contact">
      <li>
        <svg viewBox="0 0 20 22" aria-hidden="true"><rect x="5" y="1" width="10" height="20" rx="2" fill="var(--brand-orange)"/><rect x="7" y="4" width="6" height="8" fill="var(--card-black)"/></svg>
        555-204-3187
      </li>
      <li>
        <svg viewBox="0 0 20 22" aria-hidden="true"><path d="M4 4 C3 10 8 17 15 19 L18 16 L14 12 L12 14 C9 13 8 11 7 9 L9 7 L6 3 Z" fill="var(--brand-orange)"/></svg>
        555-619-4402
      </li>
      <li class="address">2240 Harbor Row</li>
      <li class="address">Marlow, FL 30912</li>
    </ul>
  </section>

  <section class="card card-back" aria-label="Business card back">
    <div class="back-brand">
      <span class="brand-dot"></span>
      <span class="brand-name">Tidal Lanes</span>
    </div>
    <div class="website">www.tidallanes.com</div>
  </section>

</body>
</html>
```